Delivery Docket urgent plus require many other designs for more stationary after this.

We need a new delivery docket design urgently as the one we have needs updating and we have changed our company name. Please do not copy the one I have uploaded as we do not feel this looks professional enough. I uploaded it as a few designers requested to see what we are currently using thank you.
It is quite complex in that we need a range of information to be on the one docket.
We are a Transport Company based in Australia that has a wide variety of items that we deliver such as water, sand and gravels and heavy equipment transport.
We would prefer to keep this design to A5 size as we will get them made into books. We are looking for a modern professional look. Although it is only a delivery docket this is given to all our customers so needs to look impressive.

We need our new logo on the docket (WTR). There will also need to be areas for our address and contact numbers, email etc these will be supplied to the winning designer to make the final adjustments so for now just put something generic in these spaces.
Needs to have an area for customer details, purchase order number, date and docket number (docket number to be in red)
Needs a section where we can list the type of product / and or service that has been provided and the amount / qty usually 3 lines will be enough for this. Need area under this where the customer can sign name and print name to say that the goods / and or services have been received.

Also required somewhere on the docket are the words, Tax Invoice will be issued based on the information provided on this docket. Conditions on back of page

We then need a separate section on the same page which we will use internally that the staff member can tear off and hand into the office. On this section it needs to have area where the driver can list km at start of job and at end with space to calculate km travelled, details of fuel purchased eg amount and litres, vehicle that is being used. also need to log down wheel bearing temps.
prime mover needs spaces as follows
Steer axel FL____________ Steer axel FR _________ 1st drive axel L_______
1st drive axel R_________ 2nd drive axel L_______ 2nd drive axel R________

For the trailers need something similar x 2 as have 2 trailers
1st axel DS_________ 1st axel PS_________ 2nd axel DS__________
2nd axel PS_________ 3rd axel DS_________ 3rd axel PS__________

I have included a few examples of designs we have used in past and ones that we like so you can get an idea of the colours we prefer, I have included some of the designs we are currently receiving for our logo that I like so you can get idea again of colours we prefer. There is much more we need designed also such as time sheets, more delivery dockets and letter heads so there is a lot of more work available to the winning designer.

Thank you

Customers

Serif
Sans Serif

Designer to choose colors to be used in the design.

• Please don't copy old docket as we do not like it and nned new info on new design thank you

```html
<!DOCTYPE html>
<html lang="en">
<head>
<meta charset="utf-8">
<title>WTR Delivery Docket</title>
<link rel="stylesheet" href="https://fonts.googleapis.com/css2?family=Roboto:ital,wght@0,400;0,500;0,700;1,700&display=swap">
<style>
  :root {
    --brand-cyan: #1bb8d8;
    --ink: #2b2b2b;
    --ink-soft: #555;
    --rule: #b9bcc0;
    --paper: #ffffff;
    --backdrop: #e4e5e7;
    --stripe: #e8eef2;
    --docket-red: #e0464b;
    --mark-dark: #1d1d1f;
  }
  * { box-sizing: border-box; margin: 0; padding: 0; }
  html, body { width: 1200px; height: 800px; overflow: hidden; }
  body {
    background: var(--backdrop);
    font-family: "Roboto", Arial, sans-serif;
    color: var(--ink);
    position: relative;
  }
  .sheet {
    position: absolute;
    top: 46px;
    width: 500px;
    height: 708px;
    background: var(--paper);
    box-shadow: 0 2px 8px rgba(0,0,0,.12);
  }
  .sheet--docket { left: 66px; }
  .sheet--driver-log { left: 634px; }

  /* Brand mark */
  .brand { display: flex; align-items: center; gap: 8px; }
  .brand__square { width: 22px; height: 22px; background: var(--mark-dark); }
  .brand__name { font-weight: 700; font-size: 40px; letter-spacing: 2px; color: var(--brand-cyan); line-height: 1; }

  /* Docket */
  .docket__topband { height: 14px; background: var(--brand-cyan); }
  .docket__header { position: relative; height: 170px; }
  .docket__header .brand { position: absolute; left: 28px; top: 26px; }
  .customer-heading {
    position: absolute; right: 0; top: 0; width: 250px; height: 22px;
    background: var(--brand-cyan); color: #fff; font-size: 13px;
    display: flex; align-items: center; justify-content: center;
  }
  .field { display: flex; align-items: flex-end; font-size: 9.5px; color: var(--ink-soft); gap: 4px; white-space: nowrap; }
  .field__line { flex: 1; min-width: 20px; border-bottom: 1px solid var(--rule); height: 10px; }
  .field__value { color: var(--docket-red); font-size: 9.5px; padding-left: 14px; }
  .order-fields { position: absolute; right: 24px; top: 34px; width: 220px; display: grid; gap: 3px; }
  .contact-fields { position: absolute; left: 28px; top: 92px; width: 440px; display: grid; gap: 3px; }
  .abn-field { position: absolute; left: 210px; top: 150px; width: 262px; }

  .line-items { position: relative; margin: 0 24px; height: 320px; border: 1px solid var(--rule); border-top: none; overflow: hidden; }
  .line-items__stripes {
    position: absolute; inset: 0;
    background: repeating-linear-gradient(to bottom, var(--stripe) 0 10px, var(--paper) 10px 20px);
  }
  .line-items__head { position: absolute; top: 0; left: 0; right: 0; height: 44px; }
  .col-head { position: absolute; background: var(--brand-cyan); color: #fff; font-size: 12px; display: flex; align-items: center; justify-content: center; }
  .col-head--qty { left: 0; width: 70px; top: 0; height: 16px; }
  .col-head--desc { left: 70px; right: 80px; top: 12px; height: 18px; }
  .col-head--amount { right: 0; width: 80px; top: 26px; height: 18px; }
  .col-rule { position: absolute; top: 0; bottom: 0; width: 1px; background: var(--rule); }
  .col-rule--qty { left: 70px; }
  .col-rule--amount { right: 80px; }
  .line-items__watermark {
    position: absolute; left: 50%; top: 52%; transform: translate(-50%, -50%);
    font-weight: 700; font-size: 130px; letter-spacing: 10px; color: rgba(27,184,216,.08);
  }

  .tax-note { margin: 14px 24px 0; text-align: center; font-size: 11px; line-height: 1.4; font-weight: 500; }
  .tax-note strong { font-style: italic; font-weight: 700; }
  .sign-off { display: flex; margin: 10px 24px 0; border: 1px solid var(--rule); height: 110px; }
  .sign-off__cell { flex: 1; position: relative; font-size: 11px; text-align: center; padding-top: 20px; }
  .sign-off__cell + .sign-off__cell { border-left: 1px solid var(--rule); }
  .sign-off__cell::after { content: ""; position: absolute; left: 22px; right: 22px; bottom: 36px; border-bottom: 1px solid var(--rule); }

  /* Driver log (tear-off, internal use) */
  .tear-line {
    position: absolute; left: 0; right: 0; top: 0; height: 0;
    border-top: 1px dashed var(--rule);
  }
  .log-section { padding: 22px 26px 0; }
  .log-section__heading {
    display: inline-block; background: var(--brand-cyan); color: #fff;
    font-size: 11.5px; font-weight: 400; padding: 3px 12px 3px 8px;
  }
  .log-grid { display: grid; grid-template-columns: repeat(3, 1fr); gap: 6px 16px; margin-top: 8px; }
  .log-grid .field { font-size: 9px; }
  .sheet--driver-log .brand { position: absolute; right: 32px; bottom: 40px; }
</style>
</head>
<body>

<section class="sheet sheet--docket" aria-label="Delivery docket">
  <div class="docket__topband"></div>
  <header class="docket__header">
    <div class="brand"><span class="brand__square"></span><span class="brand__name">WTR</span></div>
    <div class="customer-heading">Customer Details:</div>
    <div class="order-fields">
      <div class="field">Purchase Order Number:<span class="field__line"></span></div>
      <div class="field">Docket Number:<span class="field__value">2050</span><span class="field__line"></span></div>
      <div class="field">Date:<span class="field__line"></span></div>
    </div>
    <div class="contact-fields">
      <div class="field">Contact Numbers:<span class="field__line"></span></div>
      <div class="field">Address:<span class="field__line"></span></div>
      <div class="field">Email:<span class="field__line"></span></div>
    </div>
    <div class="field abn-field">ABN:<span class="field__line"></span></div>
  </header>

  <div class="line-items">
    <div class="line-items__stripes"></div>
    <div class="line-items__watermark" aria-hidden="true">WTR</div>
    <div class="col-rule col-rule--qty"></div>
    <div class="col-rule col-rule--amount"></div>
    <div class="line-items__head">
      <div class="col-head col-head--qty">Qty</div>
      <div class="col-head col-head--desc">Description</div>
      <div class="col-head col-head--amount">Amount</div>
    </div>
  </div>

  <p class="tax-note"><strong>Tax Invoice will be issued</strong> based on the information provided on this docket.<br>Conditions on back of page</p>

  <div class="sign-off">
    <div class="sign-off__cell">Print Name</div>
    <div class="sign-off__cell">Sign Name</div>
  </div>
</section>

<section class="sheet sheet--driver-log" aria-label="Driver log, tear-off section for the office">
  <div class="tear-line" aria-hidden="true"></div>
  <div class="log-section">
    <h2 class="log-section__heading">Prime Mover Needs Spaces As Follows:</h2>
    <div class="log-grid">
      <div class="field">Steer axel FL<span class="field__line"></span></div>
      <div class="field">Steer axel FR<span class="field__line"></span></div>
      <div class="field">1st drive axel L<span class="field__line"></span></div>
      <div class="field">1st drive axel R<span class="field__line"></span></div>
      <div class="field">2nd drive axel L<span class="field__line"></span></div>
      <div class="field">2nd drive axel R<span class="field__line"></span></div>
    </div>
  </div>
  <div class="log-section">
    <h2 class="log-section__heading">For The Trailers Need Something Similar X 2 As Have 2 Trailers:</h2>
    <div class="log-grid">
      <div class="field">1st axel DS<span class="field__line"></span></div>
      <div class="field">1st axel PS<span class="field__line"></span></div>
      <div class="field">2nd axel DS<span class="field__line"></span></div>
      <div class="field">2nd axel PS<span class="field__line"></span></div>
      <div class="field">3rd axel DS<span class="field__line"></span></div>
      <div class="field">3rd axel PS<span class="field__line"></span></div>
    </div>
  </div>
  <div class="log-section">
    <h2 class="log-section__heading">Vehicle, Kilometres And Fuel:</h2>
    <div class="log-grid">
      <div class="field">Vehicle<span class="field__line"></span></div>
      <div class="field">KM at start<span class="field__line"></span></div>
      <div class="field">KM at end<span class="field__line"></span></div>
      <div class="field">KM travelled<span class="field__line"></span></div>
      <div class="field">Fuel amount $<span class="field__line"></span></div>
      <div class="field">Fuel litres<span class="field__line"></span></div>
    </div>
  </div>
  <div class="brand"><span class="brand__square"></span><span class="brand__name">WTR</span></div>
</section>

</body>
</html>
```